Drone service provider needs a brilliant web design

I need a responsive web design for a new drone service company. Pelham Drone Solutions provides turnkey solutions to capture, process, and deliver actionable aerial data to customers. The design should communicate a professional company that is safe, legal and insured. I included our logo design and business card designs for reference.
*content to be supplied after design selected

Target Market(s)

We serve telecommunications, construction, government, utility infrastructure, insurance and other industries.

Industry/Entity Type

Industrial

Number of Pages Required

5+ page

Colors

Designer to choose colors to be used in the design.

Requirements
Must have
• The design should highlight professional services to include Inspections, Mapping, Consulting and Training. The site should include aerial images and video to compliment the services offered. The landing page must include following sections in order: HOME, SERVICES, ABOUT, DEMO REEL, CLIENTS, CONTACT FORM, and social media buttons (Facebook, LinkedIn, Twitter, YouTube, Instagram). Contact: 615-382-9041 info@pelhamdronesolutions-example.com Smyrna, TN
• Sitemap:
• 6 pages: Home, Inspections, Mapping, Training, Consulting, About
• HOME (Landing Page)
• • Header with logo and tab links (Home, Services, About, Contact)
• • 'CAPTURE. PROCESS. DELIVER.' tagline and 'CONTACT US' button displayed within aerial image of drone over city or construction site
• • Services section with icons, text and read more link to page
• • About section with photo and text with three icons for SAFE. LEGAL. INSURED.
• • Demo reel
• • Clients logos shown scrolling horizontally
• • Contact form
• • Footer with logo, phone, email, social media buttons
• SERVICES (4 different pages)
• • Inspections
• • Mapping
• • Consulting
• • Training
• ABOUT page
• • Company
• • Partners
• • Certifications & Associations
• • Careers
• CONTACT linked to bottom of landing page
• Would you like to receive the newsletter? Yes or No Drop-down list
Nice to have
• Photos of KVR Marlin or Corvex inspecting infrastructure, buildings, construction sites, etc. A photo of one or two pilots in vest and helmet. Free stock photos preferred but would purchase the right photo that's more relevant.
• website references:
• https://www.quillrotor-example.com/
• https://www.brentfieldworks-example.com/services
• https://www.tomaro-example.com/
• http://gantrymetric-example.com/
• http://lumbrook-example.com/
• http://fennotics-example.com/
• https://www.grebe-example.io/
Should not have
• not an aerial photography or videography service business, no blog or newsletter

```html
<!DOCTYPE html>
<html lang="en">
<head>
<meta charset="utf-8">
<title>Pelham Drone Solutions</title>
<link href="https://fonts.googleapis.com/css2?family=Montserrat:wght@600;700;800&family=Open+Sans:wght@400;600;700&display=swap" rel="stylesheet">
<style>
:root{
  --blue:#1f8fd5;
  --blue-deep:#1676b8;
  --dark:#2a2a2a;
  --white:#ffffff;
  --text:#3a3a3a;
  --muted:#8c8c8c;
  --line:#dcdcdc;
}
*{margin:0;padding:0;box-sizing:border-box}
html,body{width:1200px;height:3659px;overflow:hidden}
body{position:relative;background:var(--white);font-family:"Open Sans",Arial,sans-serif;color:var(--text)}
.abs{position:absolute}

/* header */
.site-header{left:0;top:0;width:1200px;height:160px;z-index:5}
.main-nav{left:98px;top:48px;display:flex;gap:44px;z-index:6}
.main-nav a{color:var(--white);text-decoration:none;font:700 15px "Open Sans",Arial,sans-serif;letter-spacing:.3px}
.brand{left:430px;top:32px;width:340px;text-align:center;z-index:6;font:800 30px "Montserrat",Arial,sans-serif;color:#1b1b1b;line-height:1.05;letter-spacing:.5px}
.brand small{display:block;font:800 14px "Montserrat",Arial,sans-serif;letter-spacing:2px;color:#1b1b1b}
.social{display:flex;gap:8px}
.social span{width:38px;height:38px;border:2px solid var(--white);border-radius:50%;display:block}
.header-social{left:898px;top:40px;z-index:6}

/* hero */
.hero-photo{left:0;top:110px;width:1200px;height:590px;background:linear-gradient(180deg,#8e9aa6 0%,#6f7f8e 35%,#5d6a74 65%,#4c5660 100%)}
.hero-title{left:98px;top:238px;color:var(--white);font:800 58px/1.08 "Montserrat",Arial,sans-serif;letter-spacing:.5px}
.btn-light{background:var(--white);color:var(--blue);border-radius:6px;font:600 16px "Open Sans",Arial,sans-serif;display:flex;align-items:center;justify-content:center}
.hero-btn{left:98px;top:440px;width:146px;height:52px}
.hero-arrows{left:98px;top:536px}
.hero-wave{left:0;top:560px;width:1200px;height:160px}

/* services */
.section-title{width:1200px;left:0;text-align:center;color:var(--blue);font:700 28px "Montserrat",Arial,sans-serif;letter-spacing:.5px}
.title-rule{width:56px;height:3px;background:var(--blue);left:572px}
.service{width:260px;text-align:center;top:860px}
.service-icon{width:104px;height:104px;border:2px solid var(--blue);border-radius:50%;margin:0 auto;display:flex;align-items:center;justify-content:center}
.service h3{margin-top:26px;font:700 17px "Montserrat",Arial,sans-serif;letter-spacing:2.5px;color:#333}
.service p{margin-top:12px;font-size:12.5px;line-height:1.65;color:var(--muted)}
.service a{display:block;margin-top:28px;color:var(--blue);font:600 14px "Open Sans",Arial,sans-serif;text-decoration:none}

/* about */
.about-band{left:0;top:1200px;width:1200px;height:680px}
.about-photo{left:98px;top:1347px;width:453px;height:336px;border:2px solid var(--white);background:linear-gradient(160deg,#f2e3c0 0%,#c9a878 45%,#7c6b58 100%)}
.about-inset{left:249px;top:1590px;width:356px;height:183px;border:3px solid var(--white);background:linear-gradient(135deg,#4a6b3b 0%,#2f4a27 60%,#1f3019 100%)}
.about-kicker{left:607px;top:1340px;color:var(--white);font:600 22px "Montserrat",Arial,sans-serif}
.about-title{left:607px;top:1376px;color:var(--white);font:700 35px "Montserrat",Arial,sans-serif}
.pillar{top:1466px;width:150px;color:var(--white)}
.pillar h4{margin-top:16px;font:700 20px "Montserrat",Arial,sans-serif;letter-spacing:.5px}
.pillar p{margin-top:8px;font-size:13px;line-height:1.45;color:#d8d8d8}
.about-text{left:607px;top:1655px;width:500px;font-size:11px;line-height:1.75;color:#d0d0d0}
.btn-blue{background:var(--blue);color:var(--white);font:700 12px "Montserrat",Arial,sans-serif;letter-spacing:.6px;display:flex;align-items:center;justify-content:center;border-radius:2px}
.about-btn{left:607px;top:1736px;width:138px;height:36px}

/* demo reel */
.reel{top:1969px;width:482px;height:268px;border:2px solid #333}
.reel-one{left:98px;background:linear-gradient(160deg,#bcd6e3 0%,#4fb3c4 40%,#2b8a8f 75%,#5a6d3c 100%)}
.reel-two{left:622px;background:linear-gradient(170deg,#6d8fa0 0%,#7a8c6a 40%,#5e7048 70%,#8a7a66 100%)}
.play{position:absolute;left:50%;top:50%;width:72px;height:72px;margin:-36px 0 0 -36px}

/* clients */
.divider{left:98px;top:2337px;width:1004px;height:1px;background:var(--line)}
.client{top:2403px;width:134px;height:86px;border:1px solid var(--line);display:flex;align-items:center;justify-content:center}
.client span{width:56px;height:24px;background:#cfcfcf;border-radius:3px;display:block}

/* contact */
.contact-band{left:0;top:2545px;width:1200px;height:700px;background:linear-gradient(180deg,#2196da 0%,var(--blue) 60%,var(--blue-deep) 100%)}
.contact-title{color:var(--white)}
.field{border:2px solid var(--white);border-radius:8px;color:var(--white);font:600 15px "Open Sans",Arial,sans-serif;padding:12px 12px}
.news-label{left:127px;top:3018px;color:var(--white);font:600 15px "Open Sans",Arial,sans-serif}
.submit{left:529px;top:3094px;width:144px;height:48px;font-size:15px}

/* footer */
.footer-wave{left:0;top:3130px;width:1200px;height:240px}
.footer-base{left:0;top:3360px;width:1200px;height:299px;background:var(--dark)}
.footer-brand{left:430px;top:3320px;width:340px;text-align:center;font:800 30px "Montserrat",Arial,sans-serif;color:var(--white);line-height:1.05;letter-spacing:.5px}
.footer-brand small{display:block;font:800 14px "Montserrat",Arial,sans-serif;letter-spacing:2px;color:var(--white)}
.contact-line{top:3446px;left:0;width:1200px;display:flex;justify-content:center;gap:28px;color:var(--white);font-size:19px}
.contact-line div{display:flex;align-items:center;gap:10px}
.ico-circle{width:30px;height:30px;border:2px solid var(--white);border-radius:50%;display:flex;align-items:center;justify-content:center}
.footer-nav{top:3524px;left:0;width:1200px;display:flex;justify-content:center;gap:26px;color:var(--white);font:600 14px "Open Sans",Arial,sans-serif}
.footer-nav .sep{color:#bbb}
.footer-rule{left:98px;top:3582px;width:1004px;height:1px;background:#555}
.copyright{left:98px;top:3608px;color:var(--white);font-size:13px}
.footer-social{left:912px;top:3598px}
.footer-social span{width:34px;height:34px}
</style>
</head>
<body>

<div class="abs hero-photo" role="img" aria-label="Aerial photo of a drone flying over a city construction site by the harbour"></div>

<svg class="abs site-header" viewBox="0 0 1200 160" aria-hidden="true">
  <rect x="0" y="0" width="1200" height="120" fill="#1f8fd5"/>
  <path d="M395 0 H805 L765 118 Q735 122 700 124 A100 40 0 0 1 500 124 Q465 122 435 118 Z" fill="#ffffff"/>
</svg>
<nav class="abs main-nav">
  <a href="#">HOME</a><a href="#">SERVICES</a><a href="#">ABOUT</a>
</nav>
<div class="abs brand">PELHAM<small>DRONE SOLUTIONS</small></div>
<div class="abs social header-social" aria-label="Social links"><span></span><span></span><span></span><span></span><span></span></div>

<h1 class="abs hero-title">CAPTURE.<br>PROCESS.<br>DELIVER</h1>
<a class="abs btn-light hero-btn">Contact Us</a>
<svg class="abs hero-arrows" width="70" height="30" viewBox="0 0 70 30" aria-hidden="true">
  <path d="M26 15 H4 M12 7 L4 15 L12 23" stroke="#fff" stroke-width="4" fill="none" stroke-linecap="round" stroke-linejoin="round"/>
  <path d="M44 15 H66 M58 7 L66 15 L58 23" stroke="#fff" stroke-width="4" fill="none" stroke-linecap="round" stroke-linejoin="round"/>
</svg>
<svg class="abs hero-wave" viewBox="0 0 1200 160" preserveAspectRatio="none" aria-hidden="true">
  <path d="M0 120 Q500 150 900 60 Q1080 20 1200 30 V160 H0 Z" fill="#1f8fd5" opacity=".55"/>
  <path d="M0 140 Q560 160 920 70 Q1080 38 1200 44 V160 H0 Z" fill="#1f8fd5"/>
  <path d="M0 150 Q600 168 940 88 Q1090 55 1200 62 V160 H0 Z" fill="#ffffff"/>
</svg>

<h2 class="abs section-title" style="top:744px">OUR SERVICES</h2>
<div class="abs title-rule" style="top:795px"></div>

<div class="abs service" style="left:77px">
  <div class="service-icon">
    <svg width="50" height="50" viewBox="0 0 50 50" fill="none" stroke="#1f8fd5" stroke-width="2.4" stroke-linecap="round"><rect x="10" y="6" width="30" height="38" rx="3"/><path d="M16 16 l3 3 5-6 M28 16 h6 M16 27 l3 3 5-6 M28 27 h6 M16 37 h18"/></svg>
  </div>
  <h3>INSPECTIONS</h3>
  <p>Close aerial checks of towers, roofs and sites, with clear reports delivered fast.</p>
  <a href="#">Read More &gt;</a>
</div>
<div class="abs service" style="left:336px">
  <div class="service-icon">
    <svg width="50" height="50" viewBox="0 0 50 50" fill="none" stroke="#1f8fd5" stroke-width="2.4" stroke-linejoin="round"><path d="M6 10 L18 6 L32 10 L44 6 V40 L32 44 L18 40 L6 44 Z M18 6 V40 M32 10 V44"/><path d="M25 18 a5 5 0 1 1 0.01 0 M25 28 v4"/></svg>
  </div>
  <h3>MAPPING</h3>
  <p>Accurate maps and surface models of any site, processed and ready for your team.</p>
  <a href="#">Read More &gt;</a>
</div>
<div class="abs service" style="left:595px">
  <div class="service-icon">
    <svg width="50" height="50" viewBox="0 0 50 50" fill="none" stroke="#1f8fd5" stroke-width="2.4" stroke-linejoin="round" stroke-linecap="round"><rect x="6" y="8" width="38" height="24" rx="2"/><path d="M18 40 h14 M25 32 v8 M12 16 h14 M12 22 h20"/></svg>
  </div>
  <h3>CONSULTING</h3>
  <p>Plain advice on drone programs, rules and data so your crew starts on solid ground.</p>
  <a href="#">Read More &gt;</a>
</div>
<div class="abs service" style="left:854px">
  <div class="service-icon">
    <svg width="50" height="50" viewBox="0 0 50 50" fill="none" stroke="#1f8fd5" stroke-width="2.4" stroke-linejoin="round" stroke-linecap="round"><rect x="8" y="6" width="34" height="26" rx="2"/><path d="M25 32 v8 M17 44 l8-4 8 4 M14 24 l7-7 5 4 8-9"/></svg>
  </div>
  <h3>TRAINING</h3>
  <p>Hands-on pilot training for safe, legal flights and dependable data capture in the field.</p>
  <a href="#">Read More &gt;</a>
</div>

<svg class="abs about-band" viewBox="0 0 1200 680" preserveAspectRatio="none" aria-hidden="true">
  <path d="M0 40 Q600 -30 1200 40 V620 Q600 720 0 620 Z" fill="#2a2a2a"/>
</svg>
<div class="abs about-photo" role="img" aria-label="Photo of a camera drone in flight over a city at sunset"></div>
<div class="abs about-inset" role="img" aria-label="Video still of green terraced fields seen from above">
  <svg class="play" viewBox="0 0 72 72" aria-hidden="true"><circle cx="36" cy="36" r="32" fill="none" stroke="#fff" stroke-width="4"/><path d="M29 22 L51 36 L29 50 Z" fill="#fff"/></svg>
</div>
<div class="abs about-kicker">About Us</div>
<h2 class="abs about-title">Pelham Drone Solutions</h2>

<div class="abs pillar" style="left:607px">
  <svg width="52" height="56" viewBox="0 0 52 56" fill="none" stroke="#fff" stroke-width="3" stroke-linejoin="round" stroke-linecap="round"><path d="M26 4 L46 11 V27 C46 40 37 48 26 52 C15 48 6 40 6 27 V11 Z"/><path d="M17 28 l7 7 12-14"/></svg>
  <h4>SAFE</h4>
  <p>Duis aute irure dolor in reprehenderit.</p>
</div>
<div class="abs pillar" style="left:790px">
  <svg width="56" height="56" viewBox="0 0 56 56" fill="#fff"><rect x="18" y="4" width="26" height="12" rx="2" transform="rotate(40 31 10)"/><rect x="22" y="14" width="8" height="28" transform="rotate(-50 26 28)"/><rect x="6" y="46" width="30" height="6" rx="1"/></svg>
  <h4>LEGAL</h4>
  <p>Duis aute irure dolor in reprehenderit.</p>
</div>
<div class="abs pillar" style="left:968px">
  <svg width="56" height="56" viewBox="0 0 56 56" fill="#fff"><path d="M4 26 C6 12 16 4 28 4 C40 4 50 12 52 26 C48 22 44 22 40 26 C36 22 32 22 28 26 C24 22 20 22 16 26 C12 22 8 22 4 26 Z"/><path d="M28 26 V46 a5 5 0 0 1 -10 0" stroke="#fff" stroke-width="3" fill="none" stroke-linecap="round"/></svg>
  <h4>INSURED</h4>
  <p>Duis aute irure dolor in reprehenderit.</p>
</div>
<p class="abs about-text">Nemo enim ipsam voluptatem quia voluptas sit aspernatur aut odit aut fugit, sed quia consequuntur magni dolores eos qui ratione voluptatem sequi nesciunt.</p>
<a class="abs btn-blue about-btn">READ MORE &gt;</a>

<div class="abs reel reel-one" role="img" aria-label="Demo reel still of a turquoise coastline seen from an aircraft wing">
  <svg class="play" viewBox="0 0 72 72" aria-hidden="true"><circle cx="36" cy="36" r="32" fill="none" stroke="#fff" stroke-width="4"/><path d="M29 22 L51 36 L29 50 Z" fill="#fff"/></svg>
</div>
<div class="abs reel reel-two" role="img" aria-label="Demo reel still of a waterfront neighbourhood seen from above">
  <svg class="play" viewBox="0 0 72 72" aria-hidden="true"><circle cx="36" cy="36" r="32" fill="none" stroke="#fff" stroke-width="4"/><path d="M29 22 L51 36 L29 50 Z" fill="#fff"/></svg>
</div>

<div class="abs divider"></div>
<div class="abs client" style="left:98px"><span></span></div>
<div class="abs client" style="left:273px"><span></span></div>
<div class="abs client" style="left:449px"><span></span></div>
<div class="abs client" style="left:622px"><span></span></div>
<div class="abs client" style="left:795px"><span></span></div>
<div class="abs client" style="left:968px"><span></span></div>

<div class="abs contact-band"></div>
<h2 class="abs section-title contact-title" style="top:2618px">CONTACT FORM</h2>
<div class="abs title-rule" style="top:2672px;background:#fff"></div>

<div class="abs field" style="left:127px;top:2749px;width:459px;height:48px">Name</div>
<div class="abs field" style="left:612px;top:2749px;width:462px;height:48px">Phone Number</div>
<div class="abs field" style="left:127px;top:2818px;width:947px;height:48px">Email Address</div>
<div class="abs field" style="left:127px;top:2886px;width:947px;height:98px">Message</div>
<div class="abs news-label">Would you like to receive the newsletter?</div>
<div class="abs field" style="left:451px;top:3006px;width:623px;height:49px;display:flex;justify-content:space-between;align-items:center">
  <span>Yes</span>
  <svg width="14" height="8" viewBox="0 0 14 8"><path d="M0 0 H14 L7 8 Z" fill="#fff"/></svg>
</div>
<a class="abs btn-light submit">Submit Now</a>

<svg class="abs footer-wave" viewBox="0 0 1200 240" preserveAspectRatio="none" aria-hidden="true">
  <path d="M0 40 Q300 150 700 120 Q1000 95 1200 20 V240 H0 Z" fill="#ffffff"/>
  <path d="M0 70 Q320 175 720 148 Q1000 125 1200 60 V240 H0 Z" fill="#2a2a2a"/>
</svg>
<div class="abs footer-base"></div>
<div class="abs footer-brand">PELHAM<small>DRONE SOLUTIONS</small></div>

<div class="abs contact-line">
  <div><span class="ico-circle"><svg width="16" height="12" viewBox="0 0 16 12" fill="none" stroke="#fff" stroke-width="1.6"><rect x="1" y="1" width="14" height="10"/><path d="M1 1 L8 7 L15 1"/></svg></span>info@pelhamdronesolutions-example.com</div>
  <div><span class="ico-circle"><svg width="14" height="14" viewBox="0 0 14 14" fill="#fff"><path d="M3 1 L5 4 L4 6 C5 8 6 9 8 10 L10 9 L13 11 L12 13 C6 13 1 8 1 2 Z"/></svg></span>615-382-9041</div>
</div>

<nav class="abs footer-nav">
  <span>HOME</span><span class="sep">|</span><span>ABOUT US</span><span class="sep">|</span><span>SERVICES</span><span class="sep">|</span><span>PRICING</span><span class="sep">|</span><span>BLOG</span><span class="sep">|</span><span>CONTACT US</span>
</nav>
<div class="abs footer-rule"></div>
<div class="abs copyright">Copyright © 2017 Pelham Drone Solutions. All Right Reserved</div>
<div class="abs social footer-social" aria-label="Social links"><span></span><span></span><span></span><span></span><span></span></div>

</body>
</html>
```